Stonebrace Business Card Design

The Stonebrace Co is an aggregate (crushing) equipment dealer serving Western Canadian provinces. Stonebrace is a distributor of aggregate equipment for different manufacturers.

We are looking to change and update the existing business card which has been used since the existence of the company. A copy of existing card has been attached for reference. The Stonebrace Co logo we want to remain the same and we want the green color to remain the same.

We are wanting something new with a different look. A refreshing card to show a new modern and updated look. No longer wanting to have the manufacturers on the back of the card but something more like our logo on the back of the card with a statement like "Quarry Know-How"

ideas could be:
- card can be different colors on front and back
- front or reverse of the card could possibly be the green color with the logo in black

Target Market(s)

Owners of Aggregate/Crushing companies

Contact Information for Business Card

see above

Requirements
Must have
• - logo to remain same along with same font within logo
• - green color to remain same
Nice to have
• as noted above under project description
Should not have

```html
<!DOCTYPE html>
<html lang="en">
<head>
<meta charset="utf-8">
<title>Stonebrace Business Card</title>
<link href="https://fonts.googleapis.com/css2?family=Roboto:wght@400;500;700&family=Roboto+Condensed:wght@500;700&display=swap" rel="stylesheet">
<style>
  :root {
    --brand-green: #8a8c07;
    --ink: #231f1c;
    --text-grey: #4a4a48;
    --card-white: #f3f3f1;
    --backdrop: #5a4939;
  }
  * { margin: 0; padding: 0; box-sizing: border-box; }
  html, body { width: 1200px; height: 960px; overflow: hidden; }
  body {
    background: var(--backdrop);
    position: relative;
    font-family: "Roboto", Arial, sans-serif;
  }
  .card {
    position: absolute;
    width: 600px;
    height: 343px;
    border-radius: 18px;
    overflow: hidden;
  }
  .card--front { left: 314px; top: 113px; background: var(--card-white); }
  .card--back { left: 311px; top: 472px; background: var(--brand-green); }

  .wordmark {
    position: absolute;
    display: flex;
    align-items: center;
    font-family: "Roboto", Arial, sans-serif;
    font-weight: 700;
    white-space: nowrap;
  }
  .wordmark__dot { border-radius: 50%; flex: none; }
  .card--front .wordmark { right: 42px; top: 63px; font-size: 14.5px; color: var(--ink); gap: 10px; }
  .card--front .wordmark__dot { width: 16px; height: 16px; background: var(--brand-green); }
  .card--back .wordmark { left: 0; right: 0; justify-content: center; top: 159px; font-size: 22px; color: var(--ink); gap: 14px; }
  .card--back .wordmark__dot { width: 26px; height: 26px; background: var(--ink); }

  .person {
    position: absolute;
    left: 38px; top: 158px;
    border-left: 5px solid var(--brand-green);
    padding-left: 9px;
    height: 43px;
  }
  .person__name {
    font-family: "Roboto Condensed", Arial Narrow, sans-serif;
    font-weight: 700;
    font-size: 22px;
    line-height: 22px;
    color: var(--brand-green);
  }
  .person__title {
    font-family: "Roboto", Arial, sans-serif;
    font-weight: 500;
    font-size: 14.5px;
    line-height: 21px;
    color: var(--ink);
  }
  .contact-list {
    position: absolute;
    left: 35px; top: 217px;
    list-style: none;
    font-size: 14.5px;
    line-height: 19.2px;
    color: var(--text-grey);
  }
  .contact-list li { display: flex; align-items: center; gap: 8px; }
  .contact-list svg { width: 14px; height: 14px; fill: var(--brand-green); flex: none; }
  .address {
    position: absolute;
    left: 213px; top: 278px;
    border-left: 1.5px solid var(--text-grey);
    padding-left: 18px;
    font-size: 14.5px;
    line-height: 18px;
    color: var(--text-grey);
  }
  .tagline {
    position: absolute;
    left: 0; right: 0; top: 291px;
    text-align: center;
    font-weight: 700;
    font-size: 14.5px;
    color: var(--ink);
  }
</style>
</head>
<body>
  <section class="card card--front" aria-label="Card front">
    <div class="wordmark"><span class="wordmark__dot"></span>THE STONEBRACE CO.</div>

    <div class="person">
      <p class="person__name">DALE MARSH</p>
      <p class="person__title">CEO/FOUNDER</p>
    </div>

    <ul class="contact-list">
      <li><svg viewBox="0 0 16 16" aria-hidden="true"><path d="M3.5 1l2.5 3-1.5 2c1 2 3 4 5 5l2-1.5 3 2.5-1.5 2.5C8 14.5 1.5 8 1 2.5z"/></svg>780.555.0142</li>
      <li><svg viewBox="0 0 16 16" aria-hidden="true"><path d="M4 0h8v16H4zM5.5 2v10h5V2zM7 13.2h2v1.4H7z" fill-rule="evenodd"/></svg>780.555.0187</li>
      <li><svg viewBox="0 0 16 16" aria-hidden="true"><path d="M4 1h8v4H4zM1 6h14v6h-2v3H3v-3H1zM5 10v3h6v-3z" fill-rule="evenodd"/></svg>780.555.0163</li>
      <li><svg viewBox="0 0 16 16" aria-hidden="true"><path d="M1 3h14v10H1zM2.5 4.5L8 9l5.5-4.5z" fill-rule="evenodd"/></svg>dale@stonebr.com</li>
      <li><svg viewBox="0 0 16 16" aria-hidden="true"><circle cx="8" cy="8" r="7"/><path d="M5 4c1 1 2 1 2 3s-2 1-2 3M10 3c0 2 2 2 2 4s-2 2-1 5" stroke="#f3f3f1" stroke-width="1.3" fill="none"/></svg>www.stonebrace.ca</li>
    </ul>

    <p class="address">2215- 48B Avenue<br>Kelby, Manitoba R7N 3K1</p>
  </section>

  <section class="card card--back" aria-label="Card back">
    <div class="wordmark"><span class="wordmark__dot"></span>THE STONEBRACE CO.</div>
    <p class="tagline">Quarry Know-How</p>
  </section>
</body>
</html>
```